Local water manufacturing needs a re-design to an existing label design.

We need to change an existing label design for an established water manufacturing company located in the Bahamas. We are expanding into a new 1.5L size product and would like to do so with an updated label design that incorporates an animated pink conch shell (sample included) with at least one other bright color to match the existing blue background and the pink conch shell. The final design should convey an island feel and vibe. The existing label is only a suggestion. The entire label can be completely changed.

Target Market(s)

Hotels, tourist

Industry/Entity Type

Water Manufacturing

Requirements
Must have
• Bright color that matches blue cap and pink conch shell
Nice to have
• Simple design with sleek modern look.

```html
<!DOCTYPE html>
<html lang="en">
<head>
<meta charset="utf-8">
<title>Coralis Purified Water Label</title>
<link rel="stylesheet" href="https://fonts.googleapis.com/css2?family=Poppins:wght@300;500;600&family=Montserrat:wght@500;800;900&family=Roboto+Condensed:wght@400;500&display=swap">
<style>
  :root {
    --magenta: #cc0f8a;
    --navy: #123a66;
    --ink: #1f3558;
    --white: #ffffff;
    --cream: #f6e6dc;
    --sky-top: #5fdcf7;
    --sky-low: #eefbff;
    --sea: #27c4d8;
    --sea-deep: #0aa6c4;
    --sand: #f5dfb2;
    --sand-light: #f9ecd0;
    --shell-pink: #f4a6d6;
  }
  * { margin: 0; padding: 0; box-sizing: border-box; }
  html, body { width: 720px; height: 1200px; overflow: hidden; }
  body { position: relative; background: var(--white); font-family: "Montserrat", sans-serif; }

  .beach-scene {
    position: absolute; inset: 0;
    background: linear-gradient(180deg,
      var(--sky-top) 0%, var(--sky-low) 46%,
      var(--sea-deep) 49.5%, var(--sea) 60%, var(--sand-light) 63%,
      var(--sand) 80%, var(--sand-light) 100%);
  }

  .brand-band {
    position: absolute; left: 54px; top: 0; width: 236px; height: 812px;
    background: var(--magenta);
  }
  .brand-name {
    position: absolute; left: 182px; top: 404px;
    transform: translate(-50%, -50%) rotate(-90deg);
    font-family: "Poppins", sans-serif; font-weight: 600;
    font-size: 124px; line-height: 1; color: var(--cream);
    white-space: nowrap;
  }
  .conch-art {
    position: absolute; left: 70px; top: 716px; width: 210px; height: 172px;
    border-radius: 50% 40% 45% 55%;
    background: radial-gradient(ellipse at 60% 55%, var(--shell-pink) 0%, #fbe2ee 60%, #fff3f8 100%);
  }

  .product-title {
    position: absolute; left: 326px; top: 320px;
    transform: translate(-50%, -50%) rotate(-90deg);
    white-space: nowrap; color: var(--navy);
    font-family: "Poppins", sans-serif;
  }
  .product-title h1 { font-weight: 500; font-size: 39px; line-height: 1; letter-spacing: 0.2px; }
  .product-title p {
    position: absolute; left: 0; top: 56px;
    font-weight: 300; font-size: 27px; line-height: 1; letter-spacing: 0.5px;
  }

  .info-card {
    position: absolute; left: 434px; top: 132px; width: 244px; height: 936px;
    background: var(--white); border-radius: 40px;
  }
  .info-card__content {
    position: absolute; left: 434px; top: 1068px; width: 936px; height: 244px;
    transform-origin: top left; transform: rotate(-90deg);
    color: var(--ink);
  }

  .nutrition { position: absolute; left: 48px; top: 28px; width: 390px; }
  .nutrition h2 {
    font-weight: 900; font-size: 33px; line-height: 1; color: var(--navy);
    letter-spacing: 0.3px;
  }
  .nutrition__grid {
    display: flex; gap: 6px; margin-top: 4px;
    font-family: "Roboto Condensed", sans-serif; font-size: 11.5px; line-height: 1.15;
  }
  .nutrition__col { flex: 1; }
  .rule-thick { border-top: 4px solid var(--navy); margin: 3px 0; }
  .rule { border-top: 1.5px solid var(--navy); margin: 3px 0; }
  .row { display: flex; align-items: baseline; gap: 3px; }
  .row .dots { flex: 1; border-bottom: 1.5px dotted var(--ink); transform: translateY(-3px); }
  .row--right { justify-content: flex-end; font-weight: 500; }
  .footnote { font-size: 9px; margin-top: 3px; white-space: nowrap; }

  .bottler { position: absolute; left: 492px; top: 34px; font-size: 18px; line-height: 1.5; }
  .bottler h3 { font-weight: 800; font-size: 19px; color: var(--navy); }
  .bottler p { font-weight: 500; }
  .bottler .contact-head { margin-top: 14px; }
</style>
</head>
<body>
  <div class="beach-scene" role="img" aria-label="Illustrated tropical beach with bright sky, turquoise sea and sand scattered with shells and starfish"></div>

  <div class="brand-band"></div>
  <div class="brand-name">Coralis</div>
  <div class="conch-art" role="img" aria-label="Illustration of a pink conch shell"></div>

  <div class="product-title">
    <h1>PURIFIED WATER</h1>
    <p>MINERALS ADDED</p>
  </div>

  <div class="info-card"></div>
  <div class="info-card__content">
    <section class="nutrition">
      <h2>Nutrition Facts</h2>
      <div class="nutrition__grid">
        <div class="nutrition__col">
          <div>Serving Size &nbsp; ml</div>
          <div>Serving Per Container</div>
          <div class="rule-thick"></div>
          <div>Amount Per Serving</div>
          <div>Calories &nbsp; Cal</div>
          <div class="rule"></div>
          <div class="row row--right">% Daily Value*</div>
          <div class="rule"></div>
          <div class="row"><span>Total Fat &nbsp; g</span><span class="dots"></span><span>%*</span></div>
          <div class="row"><span>Satured Fat &nbsp; g</span><span class="dots"></span><span>%*</span></div>
        </div>
        <div class="nutrition__col">
          <div class="row"><span>Sodium &nbsp; mg</span><span class="dots"></span><span>%*</span></div>
          <div class="rule"></div>
          <div class="row"><span>Total Carb &nbsp; g</span><span class="dots"></span><span>%*</span></div>
          <div class="row"><span>Dietary Fiber &nbsp; g</span><span class="dots"></span><span>%*</span></div>
          <div>Sugars &nbsp; g</div>
          <div class="rule"></div>
          <div>Protein &nbsp; g</div>
          <div class="rule"></div>
          <div class="footnote">*Percent Daily Values are based on a ( &nbsp; ) calorie diet</div>
        </div>
      </div>
    </section>

    <section class="bottler">
      <h3>Bottled by:</h3>
      <p>Marlo Ltd, t/a Coralis Water &amp; Tide Water.</p>
      <p>PO BOX TX-31820</p>
      <h3 class="contact-head">Call For More Info:</h3>
      <p>sales:555-0142</p>
      <p>office:55-0187</p>
    </section>
  </div>
</body>
</html>
```